New Business Card Design Project LORVANTI-Italy

we are LORVANTI-Italy
our company in the market for 3 years we are luxury cosmetic company and its about time for a facelift :)
i will like to have elegant luxurious and unique business card
that will give the person that get it a unique, luxurious and elegant impression
I'm VERY OPEN FOR NEW IDEAS , even duo i add a few files of things that i see on line and i like them

i add my logo as well
my website is LORVANTI.COM
(if you would like to see the main style that we have)

Target Market(s)

adult that have money :)

Industry/Entity Type

Business

Contact Information for Business Card

Name - Dario Lorvanti
Position - CEO and CO Founder
address - 4817 E Halvern
telephone - 555-384-1926
email - dario@lorvanti.com
fax - 555-384-1926
website - LORVANTI.COM

Colors
000000
959595
fbee3e
ffffff

Requirements
Must have
• big logo in GOLD color
• elegant look
• impressive
Nice to have
• not must but maybe classy pattern background
• not must but maybe emblem
• maybe clear plastic business card
Should not have
• colors
• images

```html
<!DOCTYPE html>
<html lang="en">
<head>
<meta charset="utf-8">
<title>LORVANTI-Italy Business Card</title>
<link href="https://fonts.googleapis.com/css2?family=Cinzel:wght@600&family=PT+Sans:wght@400&display=swap" rel="stylesheet">
<style>
  :root {
    --page-bg: #f9f9f9;
    --card-dark: #111111;
    --card-mid: #1d1d1d;
    --gold: #d9a92a;
    --gold-light: #f1d36a;
    --rule: #6e6a5c;
    --text-light: #ffffff;
    --icon-glyph: #161616;
  }
  * { box-sizing: border-box; margin: 0; padding: 0; }
  html, body {
    width: 1200px;
    height: 900px;
    overflow: hidden;
    background: var(--page-bg);
  }
  .canvas {
    position: relative;
    width: 1200px;
    height: 900px;
  }
  .card {
    position: absolute;
    top: 271px;
    width: 457px;
    height: 282px;
    border-radius: 14px;
    overflow: hidden;
  }
  .card--front { left: 137px; }
  .card--back { left: 627px; }
  .card__surface {
    position: absolute;
    inset: 0;
    background: linear-gradient(180deg, var(--card-mid) 0%, var(--card-dark) 55%, var(--card-mid) 100%);
  }
  .brand-mark {
    position: absolute;
    display: flex;
    align-items: center;
    justify-content: center;
    gap: 8px;
    font-family: "Cinzel", serif;
    font-weight: 600;
    color: var(--gold);
    letter-spacing: 1px;
  }
  .brand-mark__dot {
    width: 10px;
    height: 10px;
    border-radius: 50%;
    background: var(--gold);
  }
  .card--front .brand-mark {
    left: 36px;
    top: 130px;
    width: 180px;
    font-size: 20px;
  }
  .card--back .brand-mark {
    left: 0;
    top: 128px;
    width: 457px;
    font-size: 26px;
  }
  .divider {
    position: absolute;
    left: 229px;
    top: 67px;
    width: 1px;
    height: 133px;
    background: var(--rule);
  }
  .identity {
    position: absolute;
    left: 247px;
    top: 62px;
  }
  .identity__name {
    font-family: "Cinzel", serif;
    font-weight: 600;
    font-size: 18.5px;
    color: var(--gold);
    letter-spacing: 0.3px;
    line-height: 1;
  }
  .identity__role {
    margin-top: 6px;
    font-family: "PT Sans", sans-serif;
    font-size: 13px;
    color: var(--text-light);
  }
  .contact-list {
    position: absolute;
    left: 247px;
    top: 121px;
    list-style: none;
    font-family: "PT Sans", sans-serif;
    font-size: 13px;
    color: var(--text-light);
  }
  .contact-list__item {
    display: flex;
    align-items: center;
    gap: 6px;
    height: 20.7px;
  }
  .contact-list__icon {
    width: 14px;
    height: 14px;
    flex: none;
  }
  .address {
    position: absolute;
    left: 247px;
    top: 213px;
    font-family: "PT Sans", sans-serif;
    font-size: 13px;
    color: var(--text-light);
  }
</style>
</head>
<body>
<main class="canvas">

  <section class="card card--front" aria-label="Business card front">
    <div class="card__surface" role="img" aria-label="Dark brushed wood-grain card texture"></div>

    <div class="brand-mark"><span class="brand-mark__dot"></span>LORVANTI</div>

    <div class="divider"></div>

    <div class="identity">
      <p class="identity__name">DARIO LORVANTI</p>
      <p class="identity__role">CEO and CO Founder</p>
    </div>

    <ul class="contact-list">
      <li class="contact-list__item">
        <svg class="contact-list__icon" viewBox="0 0 14 14" aria-hidden="true">
          <circle cx="7" cy="7" r="7" fill="var(--gold-light)"/>
          <path d="M3.5 6.2c0-1.4 1.6-2.2 3.5-2.2s3.5.8 3.5 2.2l-1.5.3-.4-1H5.4l-.4 1z M4.5 7.5h5l.5 2.5H4z" fill="var(--icon-glyph)"/>
        </svg>
        <span>555-384-1926</span>
      </li>
      <li class="contact-list__item">
        <svg class="contact-list__icon" viewBox="0 0 14 14" aria-hidden="true">
          <circle cx="7" cy="7" r="7" fill="var(--gold-light)"/>
          <rect x="4.5" y="3.3" width="5" height="2.5" fill="var(--icon-glyph)"/>
          <rect x="3.5" y="6.2" width="7" height="3" rx="0.5" fill="var(--icon-glyph)"/>
          <rect x="4.5" y="9.5" width="5" height="1.5" fill="var(--icon-glyph)"/>
        </svg>
        <span>555-384-1926</span>
      </li>
      <li class="contact-list__item">
        <svg class="contact-list__icon" viewBox="0 0 14 14" aria-hidden="true">
          <circle cx="7" cy="7" r="7" fill="var(--gold-light)"/>
          <rect x="3.5" y="4.5" width="7" height="5" fill="var(--icon-glyph)"/>
          <path d="M3.7 4.8 7 7.3l3.3-2.5" fill="none" stroke="var(--gold-light)" stroke-width="0.8"/>
        </svg>
        <span>dario@lorvanti.com</span>
      </li>
      <li class="contact-list__item">
        <svg class="contact-list__icon" viewBox="0 0 14 14" aria-hidden="true">
          <circle cx="7" cy="7" r="7" fill="var(--gold-light)"/>
          <circle cx="7" cy="7" r="3.6" fill="none" stroke="var(--icon-glyph)" stroke-width="1"/>
          <path d="M3.4 7h7.2M7 3.4c-1.6 2-1.6 5.2 0 7.2M7 3.4c1.6 2 1.6 5.2 0 7.2" fill="none" stroke="var(--icon-glyph)" stroke-width="0.8"/>
        </svg>
        <span>LORVANTI.COM</span>
      </li>
    </ul>

    <p class="address">4817 E Halvern</p>
  </section>

  <section class="card card--back" aria-label="Business card back">
    <div class="card__surface" role="img" aria-label="Dark brushed wood-grain card texture"></div>
    <div class="brand-mark"><span class="brand-mark__dot"></span>LORVANTI</div>
  </section>

</main>
</body>
</html>
```